Business card - Harbor Crest Builders

Design a business card utilizing the given logo.
colors we like: Black, greys, Teal, blues.
Tri color card, horizontal orientation likely
Logo and name likely best on top.
Info on card:

Dennis Farrow
#8 - 4815 Alder Ridge Blvd.
Surrey, B.C. V3K 2R9

778.555.0193
dennisfarrow@tellmail.ca

Slogan: "Building Dreams"

We are a construction company that specializes in new home construction on the West coast of BC Canada. Open Concepts designs of high end homes.

```html
<!DOCTYPE html>
<html lang="en">
<head>
<meta charset="utf-8">
<title>Harbor Crest Builders – Business Card</title>
<link rel="stylesheet" href="https://fonts.googleapis.com/css2?family=Carlito:wght@400;700&display=swap">
<style>
  :root {
    --page-bg: #e6e6e6;
    --card-white: #ffffff;
    --ink: #1f1f1f;
    --band-black: #050505;
    --band-grey: #9a9a9a;
    --text-light: #ffffff;
    --rule-grey: #8c8c8c;
  }
  * { margin: 0; padding: 0; box-sizing: border-box; }
  html, body {
    width: 1200px;
    height: 1000px;
    overflow: hidden;
    background: var(--page-bg);
    font-family: "Carlito", "Calibri", sans-serif;
  }
  .business-card {
    position: absolute;
    left: 88px;
    top: 200px;
    width: 1024px;
    height: 600px;
    background: var(--card-white);
    overflow: hidden;
    box-shadow: 0 10px 30px rgba(0,0,0,0.25);
  }
  .brand {
    position: absolute;
    top: 86px;
    left: 0;
    width: 100%;
    display: flex;
    justify-content: center;
    align-items: center;
    gap: 34px;
  }
  .brand-dot {
    width: 108px;
    height: 108px;
    border-radius: 50%;
    background: var(--ink);
  }
  .brand-rule {
    width: 3px;
    height: 114px;
    background: var(--ink);
  }
  .brand-name {
    font-size: 40px;
    font-weight: 400;
    letter-spacing: 3px;
    text-transform: uppercase;
    color: var(--ink);
    white-space: nowrap;
  }
  .slogan {
    position: absolute;
    top: 252px;
    left: 0;
    width: 100%;
    text-align: center;
    font-size: 34px;
    color: var(--ink);
  }
  .lower-band {
    position: absolute;
    left: 0;
    top: 0;
    width: 1024px;
    height: 600px;
  }
  .person {
    position: absolute;
    left: 174px;
    top: 452px;
    color: var(--text-light);
  }
  .person-name {
    font-size: 32px;
    font-weight: 700;
    line-height: 1.2;
  }
  .person-title {
    font-size: 26px;
    line-height: 1.3;
  }
  .info-rule {
    position: absolute;
    left: 472px;
    top: 396px;
    width: 2px;
    height: 164px;
    background: var(--rule-grey);
  }
  .contact {
    position: absolute;
    left: 504px;
    top: 388px;
    color: var(--text-light);
    font-size: 27px;
    line-height: 42px;
  }
  .contact-address { margin-bottom: 16px; }
  .contact-line {
    display: flex;
    align-items: center;
    gap: 12px;
    line-height: 40px;
  }
  .contact-icon { width: 20px; height: 20px; flex: none; }
</style>
</head>
<body>
  <section class="business-card">
    <svg class="lower-band" viewBox="0 0 1024 600" aria-hidden="true">
      <path fill="var(--band-grey)" d="M0,392 C200,428 400,390 620,306 C800,238 930,236 1024,262 L1024,600 L0,600 Z"/>
      <path fill="var(--band-black)" d="M0,392 C200,428 410,402 630,322 C800,262 930,258 1024,284 L1024,600 L0,600 Z"/>
    </svg>

    <header class="brand">
      <span class="brand-dot"></span>
      <span class="brand-rule"></span>
      <span class="brand-name">Harbor Crest Builders</span>
    </header>

    <p class="slogan">Building Dreams</p>

    <div class="person">
      <p class="person-name">Dennis Farrow</p>
      <p class="person-title">Chief Executive</p>
    </div>

    <span class="info-rule"></span>

    <address class="contact" style="font-style:normal">
      <p class="contact-address">#8 - 4815 Alder Ridge Blvd.<br>Surrey, B.C. V3K 2R9</p>
      <p class="contact-line">
        <svg class="contact-icon" viewBox="0 0 20 20" aria-hidden="true">
          <path fill="#fff" d="M2,7 C2,3 18,3 18,7 L18,9 L14,9 L14,7 C12,6 8,6 6,7 L6,9 L2,9 Z"/>
          <path fill="#fff" d="M5,10 L15,10 L17,17 L3,17 Z"/>
          <circle cx="10" cy="13.5" r="2" fill="#000"/>
        </svg>
        778.555.0193
      </p>
      <p class="contact-line">
        <svg class="contact-icon" viewBox="0 0 20 20" aria-hidden="true">
          <rect x="2" y="5" width="16" height="11" fill="none" stroke="#fff" stroke-width="1.6"/>
          <path d="M2,5 L10,11 L18,5" fill="none" stroke="#fff" stroke-width="1.6"/>
        </svg>
        dennisfarrow@tellmail.ca
      </p>
    </address>
  </section>
</body>
</html>
```